Website design for luxury private hair salon

I'm looking for someone to use my Logo and build me a website for my webpage www.corsetresses.com.au (You can have a look at it as it has every detail I need included on it already), however I want a fresh new appearance and it to look and feel super stylish.

I am thinking colours in black, with silver or white, beautiful hair images like the ones you'll see on the current webpage - the price list as per what you already see.

I will include a copy of my biz card on here, so you can see the feel of the card, and design a website with a similar feel. It is matt black with a foil silver.

Modern, but classic and fresh. I will also need you to be able to publish it to my URL for me as I have no idea how to do this. I need it up and running pronto!

The website will need to be able to be read clearly on all devices incluing smart phones and ipads. The URL is currently registered and hosted by Norvel Web

Thinking a Home Page - large logo etc and write up on who and what we offer
Services/Price List page - as per the price list on my current webpage
Contact Page - with a built in contact form.

Target Market(s)

Middle aged, fashionable, stylish women and men who enjoy luxury hair care and styling in an upmarket location.

Industry/Entity Type

Hair And Beauty

Number of Pages Required

3 page

Font styles to use
Other font styles liked:
• see my images for my current logo

Colors
000000
b2b2b2
a54499

Requirements
Must have
• Style
• Fast turnaround
• Be viewable on all devices, PC, ipads, smart phones
• Designer able to upload it so its a running website for me to my URL
Nice to have
• Just a really feminine, stylish website which is easy to read and shows some beautiful images of perfect hair
Should not have
• Browns, reds or orange colours.

```html
<!DOCTYPE html>
<html lang="en">
<head>
<meta charset="utf-8">
<title>Contact – Silverine hair &amp; body</title>
<link rel="stylesheet" href="https://fonts.googleapis.com/css2?family=Raleway:ital,wght@0,300;0,400;0,600;1,300&family=Great+Vibes&display=swap">
<style>
  :root {
    --canvas: #e9e9ea;
    --plum: #a54499;
    --plum-deep: #8a3580;
    --ink: #000000;
    --slate: #2f2f36;
    --slate-deep: #222228;
    --footer: #1c1c21;
    --silver: #b2b2b2;
    --white: #ffffff;
  }
  * { box-sizing: border-box; margin: 0; padding: 0; }
  html, body {
    width: 1200px; height: 1200px; overflow: hidden;
    background: var(--canvas);
    font-family: "Raleway", Arial, sans-serif;
  }
  .page {
    position: absolute; left: 0; top: 205px;
    width: 1200px; height: 790px;
    background: var(--slate);
  }
  .promo-band {
    position: relative; height: 170px;
    background: linear-gradient(100deg, var(--plum-deep) 0%, var(--plum) 55%, #b75aab 100%);
    display: flex; align-items: center; justify-content: space-between;
    padding: 0 150px;
  }
  .promo-text {
    color: var(--white); font-weight: 300; font-size: 33px; line-height: 1.2;
    max-width: 560px;
  }
  .btn-outline {
    border: 2px solid var(--white); border-radius: 24px;
    color: var(--white); font-weight: 600; font-size: 20px;
    padding: 9px 26px; letter-spacing: 0.3px; text-transform: uppercase;
  }
  .contact {
    position: relative; height: 430px;
    background: linear-gradient(160deg, #36363e 0%, var(--slate) 50%, var(--slate-deep) 100%);
    text-align: center; color: var(--white);
  }
  .contact-title {
    padding-top: 70px; font-weight: 400; font-size: 44px;
  }
  .contact-title .accent {
    font-family: "Great Vibes", cursive; color: var(--plum); font-size: 50px;
  }
  .form {
    width: 420px; margin: 36px auto 0;
    display: grid; grid-template-columns: 1fr 1fr; column-gap: 24px; row-gap: 48px;
  }
  .field {
    border-bottom: 1px solid var(--silver); border-left: 1px solid var(--silver);
    height: 26px; text-align: left; padding-left: 8px;
    color: var(--silver); font-style: italic; font-weight: 300; font-size: 16px;
  }
  .field.wide { grid-column: 1 / 3; }
  .btn-send {
    display: inline-block; margin-top: 30px;
    border: 1.5px solid var(--white); border-radius: 20px;
    padding: 8px 26px; font-size: 14px; font-weight: 600;
  }
  .phones {
    margin-top: 34px; font-size: 21px; font-weight: 400; letter-spacing: 0.3px;
  }
  .phones .sep { margin: 0 14px; }
  .site-footer {
    height: 190px; background: var(--footer);
    display: flex; flex-direction: column; align-items: center; justify-content: center;
    gap: 16px; color: var(--white); font-size: 13px;
  }
  .social { display: flex; gap: 22px; }
  .social span {
    width: 18px; height: 18px; border: 1.5px solid var(--silver); border-radius: 50%;
  }
  .footer-nav a { color: var(--white); text-decoration: none; }
  .footer-nav a.current { color: var(--plum); }
  .footer-nav .bar { margin: 0 14px; }
  .legal .brand { color: var(--plum); }
</style>
</head>
<body>
  <main class="page">
    <section class="promo-band" role="img" aria-label="Soft portrait photograph behind a purple overlay">
      <p class="promo-text">Wana do something with with your Hairs? So Meet us</p>
      <span class="btn-outline">Book an appointment</span>
    </section>

    <section class="contact" role="img" aria-label="Dim photograph of hands typing on a keyboard behind the contact form">
      <h1 class="contact-title">Contact <span class="accent">us</span></h1>
      <div class="form">
        <div class="field">Name</div>
        <div class="field">E-mail</div>
        <div class="field wide">Message</div>
      </div>
      <span class="btn-send">Send</span>
      <p class="phones">ROSE&nbsp; 0400 555 118<span class="sep">|</span>TAMI&nbsp; 0400 555 742</p>
    </section>

    <footer class="site-footer">
      <div class="social"><span></span><span></span><span></span><span></span></div>
      <nav class="footer-nav">
        <a class="current" href="#">Home</a><span class="bar">|</span><a href="#">Services &amp; Price List</a><span class="bar">|</span><a href="#">Contact us</a>
      </nav>
      <p class="legal">©2017 All rights reserved. <span class="brand">Silverine hair &amp; body</span></p>
    </footer>
  </main>
</body>
</html>
```